design a construction company business card

Design business card around our logo. Card must have all the typical info: name, title, address, phone, email, business name, etc. Somewhere on the card I would like to see our motto "Built on integrity... Inspired by commitment." Consider adding a splash of bright orange to the card to complement the blues and silvers/grays in the logo. We are open to metallic inks, textures, etc. We would like to see options on both light and dark backgrounds. The font in the logo is Euro Technic Extended Regular.

```html
<!DOCTYPE html>
<html lang="en">
<head>
<meta charset="utf-8">
<title>Halvorsen Building Co. – Business Card</title>
<link rel="stylesheet" href="https://fonts.googleapis.com/css2?family=Roboto:ital,wght@0,400;0,500;0,700;1,400&display=swap">
<style>
  :root {
    --page-bg: #e4e4e4;
    --card-white: #ffffff;
    --brand-blue: #2b3f9a;
    --brand-blue-light: #1a6fc0;
    --band-blue: #2a43a0;
    --text-gray: #555a60;
    --title-gray: #80858b;
    --divider: #c9c9c9;
    --silver: #d3d6db;
    --white: #ffffff;
  }
  * { margin: 0; padding: 0; box-sizing: border-box; }
  html, body {
    width: 1125px; height: 1200px; overflow: hidden;
    background: var(--page-bg);
    font-family: "Roboto", Arial, sans-serif;
  }
  .card {
    position: absolute;
    left: 171px;
    width: 826px;
    height: 472px;
    box-shadow: 0 3px 6px rgba(0,0,0,0.25);
    overflow: hidden;
  }
  /* Front */
  .card-front { top: 106px; background: var(--card-white); }
  .brand-name {
    position: absolute;
    left: 0; width: 439px; top: 190px;
    text-align: center;
    font-size: 34px; font-weight: 700;
    color: var(--brand-blue);
    line-height: 1.15;
    letter-spacing: 1px;
  }
  .divider {
    position: absolute; left: 439px; top: 111px;
    width: 2px; height: 211px; background: var(--divider);
  }
  .contact { position: absolute; left: 483px; top: 118px; color: var(--text-gray); }
  .person-name { font-size: 31px; font-weight: 700; color: var(--brand-blue); line-height: 1.1; }
  .person-title { font-size: 20px; font-weight: 500; color: var(--title-gray); margin-top: 2px; }
  .address, .reach { font-size: 20px; line-height: 26px; margin-top: 14px; }
  .reach { margin-top: 13px; }
  .band-rule {
    position: absolute; left: 0; right: 0; top: 427px;
    height: 2px; background: var(--brand-blue);
  }
  .web-band {
    position: absolute; left: 0; right: 0; top: 432px; height: 40px;
    background: linear-gradient(90deg, var(--band-blue), #2456b3 50%, var(--band-blue));
    color: var(--white);
    font-size: 19px; letter-spacing: 10px;
    display: flex; align-items: center; justify-content: center;
  }
  /* Back */
  .card-back {
    top: 639px;
    background: radial-gradient(ellipse at 50% 38%, var(--brand-blue-light) 0%, #1f55ad 40%, var(--band-blue) 80%);
  }
  .back-name {
    position: absolute; left: 0; right: 0; top: 210px;
    text-align: center;
    font-size: 52px; font-weight: 700;
    color: var(--silver);
    letter-spacing: 2px;
  }
  .back-rule {
    position: absolute; left: 222px; width: 383px; top: 331px;
    height: 7px; background: var(--silver);
  }
  .motto {
    position: absolute; left: 0; right: 0; top: 344px;
    text-align: center;
    font-size: 20px; font-style: italic;
    color: var(--white);
  }
</style>
</head>
<body>
  <section class="card card-front">
    <div class="brand-name">HALVORSEN<br>BUILDING CO.</div>
    <div class="divider"></div>
    <div class="contact">
      <div class="person-name">MARCUS REED</div>
      <div class="person-title">CEO/FOUNDER</div>
      <div class="address">412 Birchwood Avenue<br>Fairbanks, Alaska 99701</div>
      <div class="reach">P. 907 555 0143<br>mreed@hbco.com</div>
    </div>
    <div class="band-rule"></div>
    <div class="web-band">www.hbco.com</div>
  </section>

  <section class="card card-back">
    <div class="back-name">HALVORSEN</div>
    <div class="back-rule"></div>
    <p class="motto">Built on integrity... Inspired by commitment.</p>
  </section>
</body>
</html>
```